Tolvik Commercial Cleaning is lookong for a new business card design.

A fresh new design that's professional and stylish. We need a serious upgrade to our business cards. I have included pictures of our existing ones. Our clients include professional individuals and business owners. We woupdblike something professional and upbeat. Please have fun and see what you come uo with.

Target Market(s)

Property managers, business owners, facility managers and other similar professionals

Industry/Entity Type

Janitorial

Contact Information for Business Card

Name, cell, office number, email, web address

Font styles to use
Sans Serif

Colors

Designer to choose colors to be used in the design.

Requirements
Must have
• please use the green color in our logo
Nice to have
• Bar code
Should not have
• Address

```html
<!DOCTYPE html>
<html lang="en">
<head>
<meta charset="utf-8">
<title>Tolvik Commercial Cleaning — Business Card</title>
<link rel="stylesheet" href="https://fonts.googleapis.com/css2?family=Ubuntu:wght@500;700&family=Open+Sans:wght@400&display=swap">
<style>
  :root {
    --stage: #e9e7e3;
    --card-dark: #1f1f23;
    --card-dark-deco: #2a2b30;
    --brand-green: #2fb24a;
    --green-deep: #27a043;
    --green-light: #6cc76a;
    --accent-blue: #3d78c0;
    --text-grey: #b9bcc3;
    --white: #ffffff;
  }
  * { box-sizing: border-box; margin: 0; padding: 0; }
  html, body { width: 1200px; height: 780px; overflow: hidden; }
  body {
    background: var(--stage);
    display: flex;
    align-items: center;
    justify-content: center;
    gap: 40px;
  }
  .card {
    position: relative;
    width: 540px;
    height: 309px;
    border-radius: 4px;
    overflow: hidden;
    box-shadow: 0 6px 18px rgba(0,0,0,0.18);
  }

  /* Front */
  .card-front { background: var(--card-dark); }
  .brand-name {
    position: absolute;
    left: 34px;
    top: 34px;
    font-family: "Ubuntu", sans-serif;
    font-weight: 700;
    font-size: 26px;
    color: var(--brand-green);
    letter-spacing: 0.2px;
  }
  .brand-deco {
    position: absolute;
    right: -14px;
    bottom: -26px;
    font-family: "Ubuntu", sans-serif;
    font-weight: 700;
    font-size: 130px;
    line-height: 1;
    color: var(--card-dark-deco);
  }
  .person-name {
    position: absolute;
    left: 34px;
    top: 104px;
    font-family: "Ubuntu", sans-serif;
    font-weight: 500;
    font-size: 24px;
  }
  .person-name .first { color: var(--brand-green); }
  .person-name .last { color: var(--accent-blue); }
  .contact-list {
    position: absolute;
    left: 34px;
    top: 146px;
    list-style: none;
    font-family: "Open Sans", sans-serif;
    font-size: 13px;
    color: var(--text-grey);
    line-height: 22px;
  }
  .contact-list li { display: flex; align-items: center; gap: 9px; }
  .contact-icon { width: 11px; height: 11px; flex: none; }

  /* Back */
  .card-back { background: var(--brand-green); }
  .back-pattern {
    position: absolute;
    inset: 0;
    background: linear-gradient(120deg, var(--green-deep) 0%, var(--brand-green) 55%, var(--green-light) 100%);
  }
  .back-brand {
    position: absolute;
    left: 0;
    right: 0;
    top: 50%;
    transform: translateY(-50%);
    text-align: center;
    font-family: "Ubuntu", sans-serif;
    font-weight: 700;
    font-size: 40px;
    color: var(--white);
  }
</style>
</head>
<body>
  <section class="card card-front">
    <div class="brand-deco" aria-hidden="true">Tolvik</div>
    <div class="brand-name">Tolvik Commercial Cleaning</div>
    <h1 class="person-name"><span class="first">Marco</span> <span class="last">Delaney</span></h1>
    <ul class="contact-list">
      <li>
        <svg class="contact-icon" viewBox="0 0 12 12" aria-hidden="true"><path d="M2.5 1 L4.5 1 L5.3 3.4 L4 4.4 C4.6 5.8 6.2 7.4 7.6 8 L8.6 6.7 L11 7.5 L11 9.5 C11 10.3 10.3 11 9.5 11 C5 11 1 7 1 2.5 C1 1.7 1.7 1 2.5 1 Z" fill="var(--brand-green)"/></svg>
        (512) 555-0187
      </li>
      <li>
        <svg class="contact-icon" viewBox="0 0 12 12" aria-hidden="true"><rect x="0.5" y="2" width="11" height="8" rx="1" fill="var(--brand-green)"/><path d="M1 2.8 L6 6.5 L11 2.8" fill="none" stroke="var(--card-dark)" stroke-width="1"/></svg>
        marco@tolvikclean.com
      </li>
      <li>
        <svg class="contact-icon" viewBox="0 0 12 12" aria-hidden="true"><circle cx="6" cy="6" r="5.5" fill="var(--brand-green)"/><path d="M0.8 6 H11.2 M6 0.5 C3.8 3 3.8 9 6 11.5 M6 0.5 C8.2 3 8.2 9 6 11.5" fill="none" stroke="var(--card-dark)" stroke-width="0.9"/></svg>
        www.tolvikclean.com
      </li>
    </ul>
  </section>

  <section class="card card-back">
    <div class="back-pattern" role="img" aria-label="Repeating brand wordmark pattern in shades of green"></div>
    <div class="back-brand">Tolvik</div>
  </section>
</body>
</html>
```